Create a Professional PowerPoint Slide Deck

I need a professional looking and editable PowerPoint presentation with contents based on the attached PDF.

I would like to see the following;
- add design elements to every slide (cover, title, contents etc)
- enhance the graphs or charts
- same copy will be used
I'm attaching the document to be put into powerpoint (KVRD white paper: "Haul Wise")

Target Market(s)

Executives and managers responsible for the distribution of products

Industry/Entity Type

It Professional

Font styles to use
Serif

Colors

Designer to choose colors to be used in the design.

Requirements
Must have
• The format should be portrait orientation as this may be printed on paper and converted to PDF for distribution
• Complete conversion of all pages in the attached White Paper
• Upgraded graphics and formatting
Nice to have
• Any creative ideas to make the presentation more attractive or easier to understand
• Color scheme should complement the KVRD Freightworks Logo (red and black)

```html
<!DOCTYPE html>
<html lang="en">
<head>
<meta charset="utf-8">
<title>KVRD Freightworks – Use Your Data to Improve Logistics</title>
<link href="https://fonts.googleapis.com/css2?family=Arimo:wght@400;700&display=swap" rel="stylesheet">
<style>
:root{
  --red:#e8141c;
  --black:#1a1a1a;
  --ink:#4a4a4a;
  --muted:#8a8a8a;
  --line:#f2a6a8;
  --panel:#eeeeee;
  --grey-dot:#b5b5b5;
  --stage:#e4e4e4;
  --paper:#ffffff;
  --rule:#d8d8d8;
}
*{margin:0;padding:0;box-sizing:border-box}
html,body{width:1200px;height:800px;overflow:hidden;background:var(--stage);font-family:"Arimo",Arial,sans-serif;color:var(--ink)}
.page{position:absolute;width:506px;height:675px;background:var(--paper)}
.page--left{left:57px;top:63px}
.page--right{left:633px;top:65px}
.abs{position:absolute}
.header-band{left:0;top:0;width:340px;height:70px}
.header-title{left:65px;top:33px;font-size:11.4px;font-weight:700;color:#fff;line-height:13.5px;letter-spacing:.1px}
.brand{right:28px;top:34px;display:flex;align-items:center;gap:6px}
.brand-dot{width:18px;height:18px;border-radius:50%;background:var(--red)}
.brand-name{font-size:24px;font-weight:700;color:var(--red);letter-spacing:1px}
.body-text{font-size:9.6px;line-height:11.3px;color:var(--ink)}
.justify{text-align:justify}
.fig-box{border:1px solid #e2e2e2;background:#fff;overflow:hidden}
.caption{background:#f4f4f4;border-top:1px solid var(--line)}
.caption-label{font-size:9.6px;font-weight:700;color:var(--red)}
.caption-text{font-size:7.4px;font-weight:700;color:var(--muted);line-height:8.6px}
.mini-title{font-size:6px;font-weight:700;color:#222}
.mini-label{font-size:4.6px;color:#333}
.rows{background:repeating-linear-gradient(to bottom,#9aa3b0 0 1px,transparent 1px 4.2px)}
.rows--faint{background:repeating-linear-gradient(to bottom,#c5cad2 0 1px,transparent 1px 5px)}
.map{background:linear-gradient(160deg,#cfe1f2,#dfe6d9 55%,#c9dcee)}
.footer-rule{height:1px;background:var(--line)}
.page-num{font-size:7.5px;color:var(--muted)}
.section-head{font-size:14.4px;font-weight:700;color:var(--red)}
.diagram-label{font-family:"Arimo",Arial,sans-serif;font-weight:700}
</style>
</head>
<body>

<!-- Page 05 -->
<section class="page page--left">
  <svg class="abs header-band" viewBox="0 0 340 70" aria-hidden="true">
    <polygon points="0,0 60,0 47,70 0,70" fill="var(--black)"/>
    <polygon points="60,0 338,0 318,70 47,70" fill="var(--red)"/>
  </svg>
  <div class="abs header-title">USE YOUR DATA TO IMPROVE LOGISTICS<br>PROCESSES AND PROFITS</div>
  <div class="abs brand"><span class="brand-dot"></span><span class="brand-name">KVRD</span></div>

  <p class="abs body-text justify" style="left:34px;top:120px;width:439px">KVRD takes your data and processes it through software that produces reports which yield important insights to your logistics program. These reports are reduced to Key Performance Indicators (KPI's) which are published monthly and reviewed with management to spot trends early and make necessary adjustments to your processes (Fig. 4). These reports are provided at no cost as long as you are shipping with one of KVRD's partners. If you would like to have other data included which has not been captured by the TMS, this can be done for a fee.</p>

  <div class="abs fig-box" style="left:34px;top:198px;width:138px;height:183px">
    <div class="abs mini-title" style="left:5px;top:6px">Birch Widgets: Supply Chain KPI's</div>
    <div class="abs mini-label" style="left:5px;top:16px">LTL Summary</div>
    <div class="abs rows" style="left:5px;top:23px;width:110px;height:25px"></div>
    <div class="abs mini-label" style="left:5px;top:52px">Monthly Data</div>
    <div class="abs rows" style="left:5px;top:59px;width:122px;height:78px"></div>
  </div>

  <div class="abs fig-box" style="left:182px;top:198px;width:141px;height:183px">
    <div class="abs mini-label" style="left:4px;top:6px">12 Mo Moving Total</div>
    <div class="abs rows" style="left:4px;top:13px;width:126px;height:38px"></div>
    <svg class="abs" style="left:12px;top:54px" width="100" height="78" viewBox="0 0 100 78" aria-hidden="true">
      <rect x=".5" y=".5" width="99" height="77" fill="#fff" stroke="#bbb"/>
      <g stroke="#e6e6e6" stroke-width=".5"><line x1="8" y1="15" x2="96" y2="15"/><line x1="8" y1="30" x2="96" y2="30"/><line x1="8" y1="45" x2="96" y2="45"/><line x1="8" y1="60" x2="96" y2="60"/></g>
      <polyline points="10,12 16,22 22,34 30,42 40,49 52,54 64,58 76,61 88,63 94,64" fill="none" stroke="#4d7cc2" stroke-width="1"/>
    </svg>
  </div>

  <div class="abs fig-box" style="left:332px;top:198px;width:141px;height:183px">
    <div class="abs mini-label" style="left:4px;top:6px">Top LTL Destinations, August, 2016</div>
    <div class="abs rows" style="left:4px;top:14px;width:105px;height:17px"></div>
    <div class="abs map" role="img" aria-label="Map of top destination regions" style="left:8px;top:44px;width:105px;height:61px"></div>
  </div>

  <div class="abs caption" style="left:34px;top:387px;width:440px;height:32px">
    <div class="abs caption-label" style="left:5px;top:5px">FIGURE 4.</div>
    <div class="abs caption-text" style="left:5px;top:18px">Easy to read Dashboard reports provide previously unseen insights to your logistics system</div>
  </div>

  <p class="abs body-text" style="left:34px;top:441px;width:120px">In addition to the Dashboard reports, other reports let you dig deeper to discover additional opportunities for improvement and cost savings (Fig 5). KVRD prepares and helps you interpret these reports so that you get maximum benefit from your data.</p>

  <div class="abs caption" style="left:34px;top:565px;width:125px;height:50px">
    <div class="abs caption-label" style="left:5px;top:6px">FIGURE 5.</div>
    <div class="abs caption-text" style="left:5px;top:18px;width:115px">Additional reports let you dig deeper for more sophisticated analysis</div>
  </div>

  <div class="abs fig-box" style="left:186px;top:441px;width:135px;height:177px">
    <div class="abs mini-label" style="left:7px;top:5px">Birch Widgets</div>
    <div class="abs" style="left:7px;top:14px;width:121px;height:1px;background:#333"></div>
    <div class="abs rows--faint" style="left:7px;top:17px;width:121px;height:150px"></div>
  </div>
  <div class="abs fig-box" style="left:334px;top:441px;width:139px;height:177px">
    <div class="abs mini-label" style="left:7px;top:5px">Birch Widgets</div>
    <div class="abs" style="left:7px;top:14px;width:125px;height:1px;background:#333"></div>
    <div class="abs rows--faint" style="left:7px;top:17px;width:125px;height:150px"></div>
  </div>

  <div class="abs footer-rule" style="left:34px;top:641px;width:421px"></div>
  <div class="abs page-num" style="left:463px;top:637px">05</div>
</section>

<!-- Page 06 -->
<section class="page page--right">
  <svg class="abs header-band" viewBox="0 0 340 70" aria-hidden="true">
    <polygon points="0,0 60,0 47,70 0,70" fill="var(--black)"/>
    <polygon points="60,0 338,0 318,70 47,70" fill="var(--red)"/>
  </svg>
  <div class="abs header-title">USE YOUR DATA TO IMPROVE LOGISTICS<br>PROCESSES AND PROFITS</div>
  <div class="abs brand"><span class="brand-dot"></span><span class="brand-name">KVRD</span></div>

  <p class="abs body-text" style="left:34px;top:110px;width:140px">KVRD's process is shown in Figure 5 below. The shipper uses the TMS to obtain quotes and book and track their freight. The data captured in the TMS is downloaded and processed by KVRD. Easy to read "dashboard" reports are provided to management with more comprehensive reports available as required. The results are reviewed monthly with management and recommendations for improvements in the logistics system are presented.</p>

  <div class="abs" style="left:34px;top:301px;width:133px;height:1px;background:var(--line)"></div>
  <div class="abs caption-label" style="left:39px;top:308px">FIGURE 6.</div>
  <div class="abs caption-text" style="left:39px;top:330px;width:118px">Using a TMS to quote, book and capture data then having KVRD filter and analyze the data pays dividends in process improvement and lower costs.</div>

  <svg class="abs" style="left:185px;top:109px" width="321" height="272" viewBox="0 0 321 272" role="img" aria-label="Diagram: shipper books through the TMS, which queries carriers and stores historical data">
    <rect width="321" height="272" fill="var(--panel)"/>
    <text x="254" y="15" text-anchor="middle" font-size="9.5" fill="#111" class="diagram-label">Queries /Booking</text>

    <rect x="14" y="77" width="88" height="116" fill="var(--red)"/>
    <rect x="19" y="182" width="79" height="4" fill="var(--black)"/>
    <text x="19" y="145" font-size="13.5" fill="#fff" class="diagram-label">SHIPPER</text>

    <rect x="153" y="77" width="88" height="116" fill="var(--red)"/>
    <rect x="158" y="182" width="79" height="4" fill="var(--black)"/>
    <text x="158" y="145" font-size="13.5" fill="#fff" class="diagram-label">TMS</text>

    <rect x="89" y="214" width="77" height="44" fill="var(--red)"/>
    <rect x="94" y="250" width="67" height="3" fill="var(--black)"/>
    <text x="127.5" y="241" text-anchor="middle" font-size="13.5" fill="#fff" class="diagram-label">TMS</text>

    <text x="128" y="86" text-anchor="middle" font-size="8" fill="#111" class="diagram-label">Quotes</text>
    <text x="128" y="96" text-anchor="middle" font-size="8" fill="#111" class="diagram-label">/Booking</text>
    <text x="128" y="193" text-anchor="middle" font-size="8" fill="#111" class="diagram-label">Historical</text>
    <text x="128" y="203" text-anchor="middle" font-size="8" fill="#111" class="diagram-label">Data</text>

    <g fill="none" stroke="var(--red)" stroke-width="2.2" stroke-linecap="round" stroke-linejoin="round">
      <polyline points="117,133 113,137 117,141"/><polyline points="139,133 143,137 139,141"/>
      <polyline points="181,57 185,53 189,57"/><polyline points="181,65 185,69 189,65"/>
      <polyline points="222,57 226,53 230,57"/><polyline points="222,65 226,69 230,65"/>
      <polyline points="271,55 274,52 277,55"/><polyline points="269,63 273,66 277,63"/>
      <polyline points="258,90 254,94 258,98"/><polyline points="266,90 270,94 266,98"/>
      <polyline points="258,137 254,141 258,145"/><polyline points="266,137 270,141 266,145"/>
      <polyline points="258,185 254,189 258,193"/><polyline points="266,185 270,189 266,193"/>
      <polyline points="181,212 185,208 189,212"/><polyline points="181,220 185,224 189,220"/>
      <polyline points="222,212 226,208 230,212"/><polyline points="222,220 226,224 230,220"/>
      <polyline points="270,212 273,209 276,212"/><polyline points="272,221 276,224 279,220"/>
      <polyline points="91,201 95,197 99,201"/><polyline points="91,209 95,213 99,209"/>
      <polyline points="152,201 156,197 160,201"/><polyline points="152,209 156,213 160,209"/>
    </g>

    <g font-size="11" text-anchor="middle" class="diagram-label" fill="#fff">
      <circle cx="185" cy="34" r="12" fill="var(--grey-dot)"/><text x="185" y="38">T</text>
      <circle cx="226" cy="34" r="12" fill="var(--red)"/><text x="226" y="38">T</text>
      <circle cx="278" cy="34" r="12" fill="var(--grey-dot)"/><text x="278" y="38">T</text>
      <circle cx="288" cy="94" r="12" fill="var(--grey-dot)"/><text x="288" y="98">T</text>
      <circle cx="288" cy="141" r="12" fill="var(--grey-dot)"/><text x="288" y="145">T</text>
      <circle cx="288" cy="189" r="12" fill="var(--grey-dot)"/><text x="288" y="193">T</text>
      <circle cx="185" cy="245" r="12" fill="var(--grey-dot)"/><text x="185" y="249">T</text>
      <circle cx="226" cy="245" r="12" fill="var(--grey-dot)"/><text x="226" y="249">T</text>
      <circle cx="278" cy="245" r="12" fill="var(--grey-dot)"/><text x="278" y="249">T</text>
    </g>
  </svg>

  <p class="abs body-text justify" style="left:34px;top:397px;width:440px">Bottom line, simplify your freight booking processes and reduce pricing by using a TMS provided by a 3PL. Capture the knowledge that your historical data contains, analyze it and take actions that will improve your processes and your profit.</p>
  <div class="abs" style="left:34px;top:435px;width:440px;height:1px;background:var(--rule)"></div>

  <h2 class="abs section-head" style="left:34px;top:458px">KVRD is There When You Need Help or Advice</h2>

  <p class="abs body-text justify" style="left:34px;top:484px;width:440px">At the beginning of this paper, "value" was mentioned as being beyond just the price to include reliability, ease of use, availability of help when needed and so forth. In addition to bringing added value by helping you benefit from the data you are generating with each shipment, KVRD is able to work with you when you need to switch modes or evaluate a new distribution plan. If you typically ship LTL but suddenly have a need for an expedited air shipment for an important order, KVRD can help you move that without having to start from scratch. KVRD's 3PL partners will provide the same reliable service and significant buying power whether you ship by air, ocean, truck or intermodal. International and domestic services are also easily handled.</p>

  <p class="abs body-text justify" style="left:34px;top:582px;width:440px">If you'd like to know more, contact the author, Dana Marlow, at dana@kvrdfreight.com and start harnessing your data to improve profits.</p>

  <div class="abs footer-rule" style="left:34px;top:642px;width:421px"></div>
  <div class="abs page-num" style="left:463px;top:638px">06</div>
</section>

</body>
</html>
```